Financial Services Consultant needs a business card

We need a business card for a new consulting company based in Melbourne called
"Quelbrook Insights". Tagline is Measure, Monitor, Save
We would like to see business card designs that are in line with the minimal style of the website www.quelbrook-insights.example
The font I have used on the website is Proxima Nova and would like the same or similar font used on the business card with a minimal design in line with the website Two sided with "QUELBROOK INSIGHTS" MEASURE, MONITOR, SAVE on one side and name, title and contact details on the otther
Updates

Hi All, thanks for your submissions, much appreciated.

I have recently added some colour to my webiste, it is hex #3a7b74 for those that wish to use it
Thanks

Hi all

thanks very much for your design submissions I am very impressed and they are much appreciated.

Interms of general feedback please find below;

Colour: I am trying to stick to a minimal design and colour scheme for my website which is still under construction, up to 3 colours( www.quelbrook-insights.example) it is currently black and white with a small amount of blue/green but I am open to suggestion/interpretations for a consulting company.

Card: I dont mind if it has rounded edges or straight, I was thinking about using a letterpress card if possible

Detail: the detail on the card will include; Name, Title, Mobile, Personal Email, Business Email,Web,Business Address

Once again thanks for submissions

Industry/Entity Type

Business

```html
<!DOCTYPE html>
<html lang="en">
<head>
<meta charset="utf-8">
<title>Quelbrook Insights — Business Card Front</title>
<link rel="stylesheet" href="https://fonts.googleapis.com/css2?family=Montserrat:wght@400;700&display=swap">
<style>
  :root {
    --page: #ffffff;
    --card: #ffffff;
    --card-edge: #9a9a9a;
    --ink: #231f20;
    --brand: #3a7b74;
  }
  * { margin: 0; padding: 0; box-sizing: border-box; }
  html, body {
    width: 1000px;
    height: 1200px;
    overflow: hidden;
    background: var(--page);
  }
  .canvas {
    position: relative;
    width: 1000px;
    height: 1200px;
  }
  .card {
    position: absolute;
    left: 200px;
    top: 75px;
    width: 600px;
    height: 1050px;
    background: var(--card);
    border: 1px solid var(--card-edge);
  }
  .card__bar {
    position: absolute;
    left: 52px;
    width: 498px;
    height: 37px;
  }
  .card__bar--top { top: 0; background: var(--ink); }
  .card__bar--bottom { bottom: 0; background: var(--brand); }

  .wordmark {
    position: absolute;
    left: 0;
    top: 80px;
    width: 100%;
    text-align: center;
    font-family: "Montserrat", sans-serif;
    font-weight: 700;
    font-size: 62px;
    line-height: 90px;
    letter-spacing: 0.1em;
    color: var(--brand);
  }
  .wordmark__line { display: block; padding-left: 0.1em; }

  .braces {
    position: absolute;
    left: 0;
    top: 0;
    width: 600px;
    height: 1050px;
  }
  .tagline {
    position: absolute;
    left: 118px;
    top: 428px;
    list-style: none;
    font-family: "Montserrat", sans-serif;
    font-weight: 400;
    font-size: 44px;
    line-height: 1;
    letter-spacing: 0.52em;
    color: var(--brand);
  }
  .tagline__item { height: 113px; }
</style>
</head>
<body>
<main class="canvas">
  <section class="card" aria-label="Quelbrook Insights business card, front">
    <div class="card__bar card__bar--top"></div>

    <h1 class="wordmark">
      <span class="wordmark__line">QUELBROOK</span>
      <span class="wordmark__line">INSIGHTS</span>
    </h1>

    <svg class="braces" viewBox="0 0 600 1050" aria-hidden="true">
      <g fill="none" stroke="var(--ink)" stroke-width="18">
        <path d="M125 382 H105 Q80 382 79 430 V520 Q79 558 56 560 Q79 562 79 600 V690 Q80 747 105 747 H125"/>
        <path transform="translate(601 0) scale(-1 1)" d="M125 382 H105 Q80 382 79 430 V520 Q79 558 56 560 Q79 562 79 600 V690 Q80 747 105 747 H125"/>
      </g>
    </svg>

    <ul class="tagline">
      <li class="tagline__item">MEASURE</li>
      <li class="tagline__item">MONITOR</li>
      <li class="tagline__item">SAVE</li>
    </ul>

    <div class="card__bar card__bar--bottom"></div>
  </section>
</main>
</body>
</html>
```